-Photo booth rental Web Design Project

Our business is a small photo booth rental service serving the capital region and surrounding areas. The photo booth is a portable booth that fits up to 10 guest. I am looking for a website that will have social media capabilities and also private log ins for clients to view their photo albums online after their event. We provide full service photo booth rentals for all types of parties. I am looking for something fun and unique but also professional and I am also looking to maybe somehow incorporate the age of the photo booth which was invented in 1888. I do not have the photos of our photo booth available because we are just starting up and I wanted to get everything together first but I will provide stock photo booth pictures .Thank you for your patience i know it wont be an easy task with out those things. I added a word document describing information i will need on our website, i am looking for a home page, contact us and book an event page, online gallery page, and pricing. If you need any more information please feel free to contact me. Thanks for your help and I look forward to working with you.

Target Market(s)

For everyone from brides to be for their weddings or private parties, corporate parties, school dances, charity events, community events ect

Industry/Entity Type

Business

Requirements
Nice to have
• social media sharing

```html
<!DOCTYPE html>
<html lang="en">
<head>
<meta charset="utf-8">
<title>Jolly Frames Photo Booth</title>
<link href="https://fonts.googleapis.com/css2?family=Open+Sans:wght@400;600;700;800&family=Mountains+of+Christmas:wght@700&display=swap" rel="stylesheet">
<style>
:root{
  --brown:#4a2a1e;
  --brown-deep:#3a1f15;
  --tan:#9c7d5e;
  --tan-light:#b39676;
  --accent:#c8915e;
  --ink:#3b2a22;
  --muted:#6f625b;
  --line:#d9d3cd;
  --card:#e9e7e4;
  --white:#ffffff;
}
*{box-sizing:border-box;margin:0;padding:0}
html,body{width:1200px;height:2500px;overflow:hidden}
body{position:relative;background:var(--white);font-family:"Open Sans",Arial,sans-serif;color:var(--ink)}
.abs{position:absolute}

/* header */
.site-header{left:0;top:0;width:1200px;height:115px;border-top:4px solid var(--tan);background:var(--white)}
.brand{left:140px;top:26px;display:flex;align-items:center;gap:12px;font-weight:700;font-size:30px;color:var(--brown);line-height:1}
.brand-dot{width:22px;height:22px;border-radius:50%;background:var(--brown)}
.main-nav{right:140px;top:46px;display:flex;gap:38px;font-size:13px;font-weight:600;color:var(--ink)}
.main-nav .active{color:var(--tan)}

/* hero */
.hero{left:0;top:115px;width:1200px;height:445px;background:var(--brown)}
.hero-photo{left:142px;top:147px;width:390px;height:495px;background:linear-gradient(100deg,#1d1a1a 0%,#2b2525 30%,#b8221f 45%,#c92b24 60%,#1e1b1b 75%,#2a2626 100%);z-index:2}
.hero-title{left:595px;top:230px;width:460px;white-space:nowrap;font-family:"Mountains of Christmas",Georgia,serif;font-weight:700;font-size:32px;line-height:40px;color:#f3ece5}
.hero-sub{left:595px;top:282px;font-size:16px;line-height:22px;color:var(--tan-light);white-space:nowrap}
.hero-text{left:595px;top:318px;width:440px;font-size:13px;line-height:27px;color:#f1e9e2}
.btn{display:inline-block;background:var(--tan);color:#fff;font-size:12px;font-weight:600;text-transform:uppercase;text-align:center}
.hero-btn{left:595px;top:395px;width:138px;height:52px;line-height:52px}
.hero-hump{left:900px;top:508px;width:166px;height:100px;border-radius:83px 83px 0 0;background:var(--white)}
.hero-dots{left:950px;top:536px;display:flex;gap:5px}
.hero-dots span{width:11px;height:11px;border-radius:50%;background:var(--tan)}
.hero-dots span:first-child{background:var(--brown)}

/* section headings */
.sec-head{font-size:21px;font-weight:700;text-transform:uppercase;color:var(--ink);white-space:nowrap}
.sec-head em{font-style:normal;color:var(--tan)}
.rule{height:1px;background:var(--line)}

/* welcome */
.welcome-head{left:140px;top:656px}
.welcome-rule{left:140px;top:692px;width:480px}
.welcome-text{left:140px;top:703px;width:480px;font-size:11.5px;line-height:23.5px;color:var(--muted)}
.welcome-btn{left:140px;top:838px;width:120px;height:44px;line-height:44px}
.video{left:662px;top:648px;width:396px;height:230px;border:2px solid #d8d3cf;background:#fff;padding:3px}
.video-frame{width:100%;height:100%;background:radial-gradient(ellipse at 50% 35%,#c07a3a 0%,#6a3a1c 40%,#2a160c 80%);position:relative}
.video-bar{position:absolute;left:0;right:0;bottom:0;height:34px;background:#1b1412;display:flex;align-items:center;gap:12px;padding:0 12px}
.video-track{flex:1;height:5px;background:#555;border-radius:3px;position:relative}
.video-track i{position:absolute;left:0;top:0;height:5px;width:45%;background:#ddd;border-radius:3px}
.video-time{font-size:9px;color:#ccc}
.video-hd{font-size:9px;font-weight:700;color:#9ccf3a}

/* services */
.services{left:0;top:923px;width:1200px;height:287px;background:var(--tan)}
.services-head{left:140px;top:958px;color:#fff}
.services-head em{color:#fff}
.services-head b{color:var(--brown-deep)}
.services-rule{left:140px;top:1005px;width:920px;background:#b9a184}
.services-arrows{left:1028px;top:965px}
.service{width:150px;text-align:center;top:1027px}
.service-icon{width:80px;height:80px;border-radius:50%;background:var(--brown);border:3px solid #c9b49b;margin:0 auto;display:flex;align-items:center;justify-content:center}
.service-label{margin-top:24px;font-size:12px;font-weight:600;color:#fff;text-transform:uppercase;white-space:nowrap}
.service-chev{margin-top:8px}

/* gallery & contracts */
.gallery-head{left:140px;top:1246px}
.gallery-rule{left:140px;top:1290px;width:372px}
.gallery-grid{left:140px;top:1317px;width:372px;height:233px;display:grid;grid-template-columns:repeat(3,1fr);grid-template-rows:repeat(2,1fr);gap:2px}
.contracts-head{left:587px;top:1246px}
.contracts-rule{left:587px;top:1290px;width:473px}
.contract{left:587px;width:473px;display:flex;gap:24px}
.contract-photo{width:115px;height:100px;flex:none}
.contract h3{font-size:14px;font-weight:700;color:var(--tan);text-transform:uppercase;margin-bottom:6px}
.contract p{font-size:11px;line-height:20px;color:var(--muted)}

/* add-ons */
.addons{left:140px;top:1592px;width:920px;height:75px;background:var(--tan);border-radius:8px;display:flex;align-items:center;padding:0 32px;color:#f3ece5;font-size:14px;white-space:nowrap}
.addons strong{font-size:18px;margin-right:6px}
.addons-btn{margin-left:22px;background:var(--brown);color:#fff;font-size:11px;font-weight:700;padding:11px 16px;border-radius:4px}

/* pricing */
.pricing-head{left:140px;top:1704px}
.pricing-rule{left:140px;top:1750px;width:920px}
.plan{top:1766px;width:280px;text-align:center}
.plan-name{font-size:20px;font-weight:700;color:var(--tan);height:47px;text-transform:uppercase}
.plan-card{height:224px;background:var(--card);border:1px solid #d6d2cd;position:relative;padding-top:92px}
.plan-price{position:absolute;left:82px;top:0;width:116px;height:76px;background:var(--tan);color:#fff;font-size:26px;font-weight:700;line-height:62px;clip-path:polygon(0 0,100% 0,100% 100%,50% 82%,0 100%)}
.plan-card li{list-style:none;font-size:10.5px;color:var(--muted);height:26px;line-height:26px;border-bottom:1px dotted #c3bcb5;margin:0 12px;white-space:nowrap;overflow:hidden}
.plan-card li:last-child{border-bottom:0}
.plan-cta{height:50px;line-height:50px;background:var(--brown);color:var(--accent);font-size:22px;font-weight:800;text-transform:uppercase}

/* footer */
.footer{left:0;top:2133px;width:1200px;height:297px;background:var(--brown)}
.foot-head{font-size:16px;font-weight:700;color:#e7ddd3;text-transform:uppercase;top:2182px}
.post{left:170px;display:flex;gap:14px;width:270px}
.post-date{width:50px;height:50px;border-radius:50%;background:#f1ebe5;color:var(--brown);font-size:12px;font-weight:700;text-align:center;line-height:16px;padding-top:9px;flex:none}
.post h4{font-size:13px;color:#f1ebe5;margin-bottom:2px}
.post p{font-size:10px;line-height:15px;color:#cdbfb2}
.post small{font-size:9px;color:#a89383}
.news-form{left:480px;top:2227px;width:250px;height:36px;display:flex}
.news-input{flex:1;background:#2a150e;color:#bda999;font-size:11px;line-height:36px;padding-left:14px}
.news-btn{width:62px;background:var(--tan);color:#f3ece5;font-size:10px;font-weight:700;text-align:center;line-height:36px}
.news-text{left:480px;top:2280px;width:250px;font-size:11px;line-height:19px;color:#e1d6cc}
.contact-list{left:790px;top:2222px;width:270px;list-style:none}
.contact-list li{display:flex;gap:12px;font-size:11px;line-height:16px;color:#e1d6cc;margin-bottom:14px}
.social{left:788px;top:2345px;display:flex;gap:12px}
.social span{width:36px;height:36px;border-radius:50%;border:2px solid #d9ccc0}
.bottom-bar{left:0;top:2430px;width:1200px;height:70px;background:var(--brown-deep);text-align:center;line-height:70px;font-size:12px;font-weight:600;color:#e1d6cc}
</style>
</head>
<body>

<header class="site-header abs">
  <div class="brand abs"><span class="brand-dot"></span>Jolly Frames</div>
  <nav class="main-nav abs">
    <span class="active">HOME</span><span>PRICING</span><span>CONTACT US</span><span>BOOK AN EVENT</span><span>CLIENT LOG IN</span>
  </nav>
</header>

<section class="hero abs"></section>
<div class="hero-photo abs" role="img" aria-label="A couple posing beside a black and red portable photo booth"></div>
<h1 class="hero-title abs">JOLLY FRAMES PHOTO BOOTH</h1>
<p class="hero-sub abs">Family owned and operated photo booth rental company</p>
<p class="hero-text abs">Lorem ipsum dolor sit amet, consectetuer adipiscing elit. Aenean commodo ligula eget dolor. Aenean massa.</p>
<a class="btn hero-btn abs">Book an event</a>
<div class="hero-hump abs"></div>
<div class="hero-dots abs"><span></span><span></span><span></span><span></span></div>

<h2 class="sec-head welcome-head abs">Welcome to <em>Jolly Frames Photo Booth</em></h2>
<div class="rule welcome-rule abs"></div>
<p class="welcome-text abs">Lorem ipsum dolor sit amet, consectetuer adipiscing elit. Aenean commodo ligula eget dolor. Aenean massa. Cum sociis natoque penatibus et magnis dis parturient montes, nascetur ridiculus mus. Donec quam felis, ultricies nec, pellentesque eu, pretium quis, sem. Nulla consequat massa quis enim. Donec pede justo, fringilla vel, aliquet nec, vulputate eget, arcu. In enim justo, rhoncus ut, imperdiet a, venenatis vitae, justo.</p>
<a class="btn welcome-btn abs">More info</a>
<div class="video abs">
  <div class="video-frame" role="img" aria-label="Video still of a candlelit reception table with red roses">
    <div class="video-bar">
      <svg width="10" height="12" viewBox="0 0 10 12"><path d="M0 0L10 6L0 12Z" fill="#fff"/></svg>
      <svg width="14" height="12" viewBox="0 0 14 12"><path d="M0 4H3L7 0V12L3 8H0Z" fill="#fff"/><path d="M9 3Q12 6 9 9" stroke="#fff" fill="none"/></svg>
      <div class="video-track"><i></i></div>
      <span class="video-time">01:34</span>
      <span class="video-hd">HD</span>
      <svg width="12" height="12" viewBox="0 0 12 12"><path d="M1 5V1H5M7 1H11V5M11 7V11H7M5 11H1V7" stroke="#fff" fill="none" stroke-width="1.5"/></svg>
    </div>
  </div>
</div>

<section class="services abs"></section>
<h2 class="sec-head services-head abs"><b>Our</b> <em>Services</em></h2>
<div class="rule services-rule abs"></div>
<svg class="services-arrows abs" width="30" height="16" viewBox="0 0 30 16"><path d="M8 2L2 8L8 14M22 2L28 8L22 14" stroke="#fff" stroke-width="2.5" fill="none"/></svg>

<div class="service abs" style="left:105px">
  <div class="service-icon"><svg width="36" height="36" viewBox="0 0 36 36" fill="#fff"><circle cx="11" cy="8" r="4"/><circle cx="25" cy="8" r="4"/><path d="M6 14H16V24H14V34H8V24H6Z"/><path d="M25 14L31 28H27V34H23V28H19Z"/></svg></div>
  <div class="service-label">Weddings</div>
  <svg class="service-chev" width="12" height="8" viewBox="0 0 12 8"><path d="M1 1L6 6L11 1" stroke="#fff" stroke-width="2" fill="none"/></svg>
</div>
<div class="service abs" style="left:233px">
  <div class="service-icon"><svg width="36" height="36" viewBox="0 0 36 36" fill="#fff"><rect x="6" y="18" width="24" height="12" rx="2"/><rect x="3" y="30" width="30" height="3"/><rect x="17" y="9" width="2" height="8"/><path d="M18 3Q21 6 18 8Q15 6 18 3Z"/></svg></div>
  <div class="service-label">Birthday Parties</div>
  <svg class="service-chev" width="12" height="8" viewBox="0 0 12 8"><path d="M1 1L6 6L11 1" stroke="#fff" stroke-width="2" fill="none"/></svg>
</div>
<div class="service abs" style="left:367px">
  <div class="service-icon"><svg width="38" height="36" viewBox="0 0 38 36" fill="#fff"><path d="M19 6L37 14L19 22L1 14Z"/><path d="M9 18V26Q19 32 29 26V18L19 23Z"/><rect x="33" y="14" width="2" height="12"/></svg></div>
  <div class="service-label">Graduations</div>
  <svg class="service-chev" width="12" height="8" viewBox="0 0 12 8"><path d="M1 1L6 6L11 1" stroke="#fff" stroke-width="2" fill="none"/></svg>
</div>
<div class="service abs" style="left:500px">
  <div class="service-icon"><svg width="36" height="36" viewBox="0 0 36 36" fill="#fff"><path d="M17 14Q19 24 15 30H20Q22 22 19 14Z"/><path d="M18 14Q10 6 4 12Q11 9 18 14Q14 4 22 4Q18 8 18 14Q26 6 32 12Q25 10 18 14Z"/><ellipse cx="18" cy="31" rx="14" ry="3"/></svg></div>
  <div class="service-label">Holiday Parties</div>
  <svg class="service-chev" width="12" height="8" viewBox="0 0 12 8"><path d="M1 1L6 6L11 1" stroke="#fff" stroke-width="2" fill="none"/></svg>
</div>
<div class="service abs" style="left:638px">
  <div class="service-icon"><svg width="36" height="36" viewBox="0 0 36 36" fill="#fff"><path d="M13 8H23V12H21V10H15V12H13Z"/><rect x="4" y="12" width="28" height="18" rx="2"/></svg></div>
  <div class="service-label">Corporate Parties</div>
  <svg class="service-chev" width="12" height="8" viewBox="0 0 12 8"><path d="M1 1L6 6L11 1" stroke="#fff" stroke-width="2" fill="none"/></svg>
</div>
<div class="service abs" style="left:778px">
  <div class="service-icon"><svg width="36" height="36" viewBox="0 0 36 36"><circle cx="18" cy="21" r="10" stroke="#fff" stroke-width="4" fill="none"/><path d="M13 6H23L18 11Z" fill="#fff"/></svg></div>
  <div class="service-label">Bridal Showers</div>
  <svg class="service-chev" width="12" height="8" viewBox="0 0 12 8"><path d="M1 1L6 6L11 1" stroke="#fff" stroke-width="2" fill="none"/></svg>
</div>
<div class="service abs" style="left:925px">
  <div class="service-icon"><svg width="36" height="36" viewBox="0 0 36 36" fill="#fff"><ellipse cx="18" cy="13" rx="9" ry="11"/><path d="M16 24H20L18 27Z"/><path d="M18 27Q15 31 18 35" stroke="#fff" fill="none"/></svg></div>
  <div class="service-label">Anniversaries</div>
  <svg class="service-chev" width="12" height="8" viewBox="0 0 12 8"><path d="M1 1L6 6L11 1" stroke="#fff" stroke-width="2" fill="none"/></svg>
</div>

<h2 class="sec-head gallery-head abs">Picture <em>Gallery</em></h2>
<div class="rule gallery-rule abs"></div>
<div class="gallery-grid abs">
  <div role="img" aria-label="Event photo in a dark room" style="background:linear-gradient(135deg,#1c2a3a,#3c4a5c)"></div>
  <div role="img" aria-label="Banquet hall with chandeliers" style="background:linear-gradient(135deg,#a36a2a,#e0b060)"></div>
  <div role="img" aria-label="Dance floor with purple lights" style="background:linear-gradient(135deg,#3a1a6a,#b03a7a)"></div>
  <div role="img" aria-label="Guests at a party table" style="background:linear-gradient(135deg,#6a8a4a,#d0a080)"></div>
  <div role="img" aria-label="Friends posing with sunglasses" style="background:linear-gradient(135deg,#c8a080,#e8d0b8)"></div>
  <div role="img" aria-label="Guests laughing at an event" style="background:linear-gradient(135deg,#5a4030,#b08060)"></div>
</div>

<h2 class="sec-head contracts-head abs">Sign <em>Contracts</em></h2>
<div class="rule contracts-rule abs"></div>
<div class="contract abs" style="top:1317px">
  <div class="contract-photo" role="img" aria-label="Guests smiling at a party" style="background:linear-gradient(135deg,#c05a3a,#e8c0a0)"></div>
  <div><h3>Lorem ipsum dolor sit amet,</h3><p>Ligula eget dolor aenean massa cum sociis natoque penatibus et magnis dis parturient montes nascetur ridiculus mus donec quam felis ultricies nec pellentesque eu magna.</p></div>
</div>
<div class="contract abs" style="top:1450px">
  <div class="contract-photo" role="img" aria-label="Guests celebrating outdoors" style="background:linear-gradient(135deg,#3a6a3a,#6a8ab0)"></div>
  <div><h3>Lorem ipsum dolor sit amet,</h3><p>Ligula eget dolor aenean massa cum sociis natoque penatibus et magnis dis parturient montes nascetur ridiculus mus donec quam felis ultricies nec pellentesque eu magna.</p></div>
</div>

<div class="addons abs"><strong>ADD ON'S:</strong> Magnet photo strip frames, stand up acrylic photo strip frames ONLY $100 <span class="addons-btn">DEPOSIT</span></div>

<h2 class="sec-head pricing-head abs">Pricing <em>Information</em></h2>
<div class="rule pricing-rule abs"></div>

<div class="plan abs" style="left:140px">
  <div class="plan-name">Standard</div>
  <div class="plan-card"><div class="plan-price">$675</div>
    <ul><li>3 hours of service</li><li>set up &amp; removal</li><li>A friendly booth attendant guestbook</li><li>dvd or usb flash drive of pictures, unlimited prints</li><li>online gallery, digital backdrop</li></ul>
  </div>
  <div class="plan-cta">Sign up now</div>
</div>
<div class="plan abs" style="left:460px">
  <div class="plan-name">Ultimate</div>
  <div class="plan-card"><div class="plan-price">$850</div>
    <ul><li>3 hours of service</li><li>set up &amp; removal</li><li>A friendly booth attendant guestbook</li><li>dvd or usb flash drive of pictures, unlimited prints</li><li>online gallery, digital backdrop</li></ul>
  </div>
  <div class="plan-cta">Sign up now</div>
</div>
<div class="plan abs" style="left:778px">
  <div class="plan-name">Extreme</div>
  <div class="plan-card"><div class="plan-price">$975</div>
    <ul><li>3 hours of service</li><li>set up &amp; removal</li><li>A friendly booth attendant guestbook</li><li>dvd or usb flash drive of pictures, unlimited prints</li><li>online gallery, digital backdrop</li></ul>
  </div>
  <div class="plan-cta">Sign up now</div>
</div>

<footer class="footer abs"></footer>
<h3 class="foot-head abs" style="left:170px">Blog</h3>
<div class="post abs" style="top:2230px">
  <div class="post-date">09<br>OCT</div>
  <div><h4>Aenean Adipiscing Etiam</h4><p>Etiam porta sem malesuada magna lorem eros mollis euismod.</p><small>Journal | 3 Comments</small></div>
</div>
<div class="post abs" style="top:2325px">
  <div class="post-date">09<br>OCT</div>
  <div><h4>Aenean Adipiscing Etiam</h4><p>Etiam porta sem malesuada magna lorem eros mollis euismod.</p><small>Journal | 3 Comments</small></div>
</div>

<h3 class="foot-head abs" style="left:480px">News letter sign up</h3>
<div class="news-form abs"><span class="news-input">Email</span><span class="news-btn">SIGNUP</span></div>
<p class="news-text abs">Lorem ipsum dolor sit amet, consectetur adipiscing elit. Phasellus sollicitudin sem nec turpis eget lobortis fermentum. Integer consequat, turpis eget lobortis.</p>

<h3 class="foot-head abs" style="left:790px">Contact us</h3>
<ul class="contact-list abs">
  <li><svg width="12" height="16" viewBox="0 0 12 16"><path d="M6 0A6 6 0 0 1 12 6C12 10 6 16 6 16S0 10 0 6A6 6 0 0 1 6 0Z" fill="#c9b49b"/><circle cx="6" cy="6" r="2" fill="#4a2a1e"/></svg><span>Address: 1234 Street Name, City Name, AB 12345</span></li>
  <li><svg width="12" height="14" viewBox="0 0 12 14"><rect x="1" y="0" width="10" height="14" rx="2" fill="#c9b49b"/><rect x="3" y="2" width="6" height="7" fill="#4a2a1e"/></svg><span>Phone: (88) 123-4567</span></li>
  <li><svg width="14" height="10" viewBox="0 0 14 10"><rect width="14" height="10" fill="#c9b49b"/><path d="M0 0L7 6L14 0" stroke="#4a2a1e" fill="none"/></svg><span>Email: hello@jollyframes.example</span></li>
</ul>
<div class="social abs"><span></span><span></span><span></span><span></span></div>

<div class="bottom-bar abs">Copyright © 2014 Jolly Frames | All rights reserved.</div>

</body>
</html>
```